New eyelid plastic surgery office needs a business card design-Eyelid Care Partners of the Brenton

I recently used PixelForge for my logo design and was very pleased with creativity and results. It was a difficult decision for me. Now I would like to create a business card based on this logo, which I will attach.

The text should be easily legible as some of my patients have difficulty seeing, but I would like a subtle, sophisticated artistry also evident to make the card memorable. Would like the card based on a similar color scheme as the logo but the inverse or other complementary colors may prove interesting
Updates

A good question was asked...my concern about my visually impaired patients was really my desire to avoid italicized or calligraphic type fonts that may be hard to read. Standard font size for a business card would be fine. Thanks!

Thank you so much for the great work so far. I wanted to give you my particular contact information to see if that would change the look of the cards. Martin Delacourt, MD Address: 2718 Harborview Lane, Suite 206 Wilmington, NC 28517 Phone: 910-555-0193 Fax: 910-555-0194 Website: www.brentonlidstudio.example Please delete the email slot from the card. Thanks so much!

Industry/Entity Type

Plastic

```html
<!DOCTYPE html>
<html lang="en">
<head>
<meta charset="utf-8">
<title>Eyelid Care Partners of the Brenton – Business Card</title>
<link rel="stylesheet" href="https://fonts.googleapis.com/css2?family=Tenor+Sans&family=Libre+Baskerville:wght@700&family=Arimo:wght@400;700&display=swap">
<style>
  :root {
    --backdrop: #1e2826;
    --cyan: #33eef0;
    --cyan-soft: #bff9fa;
    --white: #ffffff;
    --navy: #1c4f95;
    --maroon: #7d1414;
    --band-dark: #3e0c0b;
    --band-mid: #8a2320;
    --gold: #d8b64e;
    --ink: #1b1b1b;
  }
  * { margin: 0; padding: 0; box-sizing: border-box; }
  html, body {
    width: 1200px;
    height: 888px;
    overflow: hidden;
    background: var(--backdrop);
  }
  .stage {
    position: relative;
    width: 1200px;
    height: 888px;
  }
  .card {
    position: absolute;
    left: 120px;
    top: 170px;
    width: 960px;
    height: 548px;
    overflow: hidden;
    box-shadow: 0 18px 40px rgba(0,0,0,.55);
  }
  .card__top {
    position: absolute;
    inset: 0 0 auto 0;
    height: 330px;
    background: radial-gradient(ellipse 55% 75% at 48% 48%, var(--white) 0%, var(--cyan-soft) 45%, var(--cyan) 100%);
  }
  .card__bottom {
    position: absolute;
    inset: 378px 0 0 0;
    background: linear-gradient(90deg, var(--cyan) 0%, var(--white) 22%, var(--white) 62%, var(--cyan-soft) 85%, var(--cyan) 100%);
  }
  .brand {
    position: absolute;
    left: 110px;
    top: 78px;
    font-family: "Tenor Sans", sans-serif;
    font-weight: 400;
    color: var(--navy);
    text-transform: uppercase;
    line-height: 1;
    white-space: nowrap;
  }
  .brand__line1 { display: block; font-size: 52px; letter-spacing: 1px; }
  .brand__line2 { display: block; font-size: 34px; margin-top: 12px; letter-spacing: 1px; }
  .tagline {
    position: absolute;
    left: 0;
    right: 0;
    top: 262px;
    text-align: center;
    font-family: "Libre Baskerville", serif;
    font-weight: 700;
    font-size: 32px;
    line-height: 40px;
    color: var(--maroon);
    white-space: nowrap;
  }
  .ornament-band {
    position: absolute;
    left: 0;
    right: 0;
    top: 330px;
    height: 48px;
    background: linear-gradient(180deg, var(--band-dark) 0%, var(--band-mid) 50%, var(--band-dark) 100%);
    border-top: 2px solid var(--gold);
    border-bottom: 2px solid var(--gold);
  }
  .contact {
    position: absolute;
    left: 70px;
    top: 394px;
    display: grid;
    grid-template-columns: 92px 20px auto;
    row-gap: 2px;
    align-items: baseline;
    font-family: "Arimo", sans-serif;
    color: var(--ink);
    white-space: nowrap;
  }
  .contact__label, .contact__sep, .contact__value {
    font-weight: 700;
    font-size: 17px;
    line-height: 22px;
  }
  .contact__name { font-size: 24px; line-height: 28px; }
</style>
</head>
<body>
<main class="stage">
  <article class="card">
    <div class="card__top"></div>
    <div class="card__bottom"></div>

    <h1 class="brand">
      <span class="brand__line1">Eyelid Care Partners</span>
      <span class="brand__line2">of the Brenton</span>
    </h1>

    <p class="tagline">New eyelid plastic surgery office</p>

    <div class="ornament-band" role="img" aria-label="Band of repeating gold floral ornaments on deep red"></div>

    <dl class="contact">
      <dt class="contact__label">Contact</dt><span class="contact__sep">:</span>
      <dd class="contact__value contact__name">Martin Delacourt, MD</dd>
      <dt class="contact__label">Address</dt><span class="contact__sep">:</span>
      <dd class="contact__value">2718 Harborview Lane, Suite 206 Wilmington, NC 28517</dd>
      <dt class="contact__label">Phone</dt><span class="contact__sep">:</span>
      <dd class="contact__value">910 - 555 - 0193</dd>
      <dt class="contact__label">Fax</dt><span class="contact__sep">:</span>
      <dd class="contact__value">910 - 555 - 0194</dd>
      <dt class="contact__label">web</dt><span class="contact__sep">:</span>
      <dd class="contact__value">www.brentonlidstudio.example</dd>
    </dl>
  </article>
</main>
</body>
</html>
```